K7 Electrical Services Ltd Web design

I require a web site for my new electrical contracting company. We are customer service orientated. Offering high value electrical installations, design and maintenance. Focused on custom residential and commercial upgrading. Lighting design and application are paramount in our company's services. Industry leading product use and integration are always on the forefront with our customer client services. As well as energy efficiency.

Target Market(s)

Homebuilders, General Contractors, Property management companies, clients, individuals,

Industry/Entity Type

Electric Company

Coding

Coded - Design and coding required

Number of Pages Required

3 page

Requirements
Must have
• Classic, modern, edgy but not trendy . Appeals to the masse.
• 3 page
• home page
• about page
• gallery page
• ability to contact from the webiste
Nice to have
• open to all types of designs that are relative to the construction industry.
• Black, Grey, metallic ice blue and deep purple colours from the logo.
Should not have
• anything cheesy with cartoon light bulb images.

```html
<!DOCTYPE html>
<html lang="en">
<head>
<meta charset="utf-8">
<title>K7 Electrical Services</title>
<link rel="stylesheet" href="https://fonts.googleapis.com/css2?family=Exo+2:wght@500;600;700&family=Lato:wght@400;700&display=swap">
<style>
:root{
  --purple:#5c2a88;
  --purple-dark:#4a1f72;
  --ink:#2b2b2b;
  --text:#555;
  --muted:#9a9a9a;
  --light:#efefef;
  --white:#fff;
  --black:#000;
  --line:#dcdcdc;
}
*{box-sizing:border-box;margin:0;padding:0}
html,body{width:1200px;height:3077px;overflow:hidden}
body{font-family:"Lato",sans-serif;color:var(--text);background:var(--white);position:relative}
.heading{font-family:"Exo 2",sans-serif;font-weight:600;text-transform:uppercase}
.btn{position:absolute;display:flex;align-items:center;justify-content:center;background:var(--purple);color:var(--white);font-family:"Exo 2",sans-serif;font-weight:600;font-size:20px;text-transform:uppercase}
.photo{position:absolute}
section,header,footer{position:absolute;left:0;width:1200px}

/* header */
.site-header{top:0;height:105px;background:var(--white)}
.brand{position:absolute;left:78px;top:28px;display:flex;align-items:center;gap:10px;font-family:"Exo 2",sans-serif;font-weight:700;font-size:22px;color:var(--purple);letter-spacing:1px}
.brand-mark{width:26px;height:26px;background:var(--purple)}
.nav{position:absolute;top:0;right:0;height:105px;display:flex;font-size:16px;color:var(--ink)}
.nav a{position:absolute;top:0;height:105px;line-height:105px;text-decoration:none;color:var(--ink);white-space:nowrap}
.nav .active{background:var(--purple);color:var(--white);width:90px;text-align:center;left:652px}

/* hero */
.hero{top:105px;height:572px;background:linear-gradient(135deg,#3b3a36 0%,#6a6355 35%,#2e2c2a 65%,#4b4a4a 100%)}
.hero-title{position:absolute;top:150px;width:100%;text-align:center;font-size:58px;color:var(--white)}
.hero-sub{position:absolute;top:227px;left:260px;width:680px;text-align:center;font-size:17px;line-height:29px;color:#eee}
.hero-arrow{position:absolute;top:260px;width:45px;height:34px;background:var(--purple);color:var(--white);display:flex;align-items:center;justify-content:center}

/* services */
.service{position:absolute;top:564px;width:333px}
.service-head{height:133px;background:var(--purple);color:var(--white);text-align:center;padding:24px 22px 0}
.service-head h3{font-size:21px;margin-bottom:14px}
.service-head p{font-size:14px;line-height:24px}
.service .photo{position:static;height:210px}

/* welcome */
.welcome{top:677px;height:625px;background:var(--light);text-align:center}
.welcome h2{position:absolute;top:284px;width:100%;font-size:42px;color:var(--purple)}
.welcome p{position:absolute;left:190px;width:820px;font-size:14px;line-height:30px}

/* gallery */
.gallery{top:1302px;height:435px}
.section-title{position:absolute;font-size:42px;color:var(--purple)}
.gallery-intro{position:absolute;left:78px;top:117px;width:660px;font-size:15px;line-height:28px}
.slide-btn{position:absolute;top:74px;width:42px;height:41px;background:var(--purple);display:flex;align-items:center;justify-content:center}

/* about */
.about{top:1737px;height:468px;background:linear-gradient(90deg,#1c1c1e 0%,#2f2f33 55%,#3a3a3e 100%);overflow:hidden}
.about p{position:absolute;left:78px;top:174px;width:500px;font-size:15px;line-height:30px;color:#e8e8e8}

/* contact */
.contact{top:2205px;height:513px;text-align:center}
.contact p{position:absolute;left:220px;width:760px;top:108px;font-size:14px;line-height:28px}
.contact h4{position:absolute;top:186px;width:100%;font-family:"Exo 2",sans-serif;font-weight:600;font-size:20px;color:var(--purple)}
.field{position:absolute;border:1px solid var(--line);background:var(--white);font-size:12px;color:var(--muted);text-align:left;padding:14px 12px}
.field.focus{border:2px solid var(--purple);color:var(--purple);font-weight:700}

/* footer */
.site-footer{top:2718px;height:359px;background:var(--black);text-align:center;color:#ccc}
.footer-brand{position:absolute;top:70px;left:0;width:100%;display:flex;justify-content:center;align-items:center;gap:14px;font-family:"Exo 2",sans-serif;font-weight:700;font-size:40px;color:var(--purple);letter-spacing:2px}
.footer-brand .brand-mark{width:44px;height:44px}
.social{position:absolute;top:189px;width:52px;height:52px;border-radius:50%}
.footer-links{position:absolute;top:264px;width:100%;font-size:13px}
.footer-links span{padding:0 16px;border-left:1px solid #777}
.footer-links span:first-child{border-left:0}
.copyright{position:absolute;top:294px;width:100%;font-size:13px}
</style>
</head>
<body>

<header class="site-header">
  <div class="brand"><span class="brand-mark"></span>K7 ELECTRICAL SERVICES</div>
  <nav class="nav">
    <a class="active" href="#">HOME</a>
    <a href="#" style="left:773px">ABOUT US</a>
    <a href="#" style="left:882px">GALLERY</a>
    <a href="#" style="left:980px">CONTACT US</a>
    <svg style="position:absolute;left:1104px;top:43px" width="20" height="20" viewBox="0 0 20 20"><circle cx="8" cy="8" r="6" fill="none" stroke="#5c2a88" stroke-width="3"/><line x1="12.5" y1="12.5" x2="18" y2="18" stroke="#5c2a88" stroke-width="3"/></svg>
  </nav>
</header>

<section class="hero" role="img" aria-label="Electrician testing a panel with a multimeter">
  <h1 class="heading hero-title">Electrical Services</h1>
  <p class="hero-sub">Offering high value electrical installations, design and maintenance. Focused on custom residential and commercial upgrading</p>
  <a class="btn" style="left:517px;top:301px;width:166px;height:49px">Contact Us</a>
  <span class="hero-arrow" style="left:0">&laquo;</span>
  <span class="hero-arrow" style="right:0">&raquo;</span>
</section>

<section class="welcome">
  <h2 class="heading">Welcome to Electrical Services</h2>
  <p style="top:352px">Lorem Ipsum is simply dummy text of the printing and typesetting industry. Lorem Ipsum has been the industry's standard dummy text ever since the 1500s, when an unknown printer took a galley.</p>
  <p style="top:415px">Lorem Ipsum is simply dummy text of the printing and typesetting industry. Lorem Ipsum has been the industry's standard dummy text ever since the 1500s, when an unknown printer took a galley of type and scrambled it to make a type specimen book. It has survived not only five centuries, but also the leap into.</p>
  <a class="btn" style="left:517px;top:511px;width:166px;height:51px">Learn More</a>
</section>

<div class="service" style="left:78px">
  <div class="service-head"><h3 class="heading">Electrical Installations</h3><p>Lorem Ipsum is the text simply dummy text of the printing and typesetting industry.</p></div>
  <div class="photo" role="img" aria-label="Electrician writing notes beside an open switchboard" style="background:linear-gradient(135deg,#3c4a5c,#6f7f8f 50%,#2c3440)"></div>
</div>
<div class="service" style="left:433px">
  <div class="service-head"><h3 class="heading">Design</h3><p>Lorem Ipsum is the text simply dummy text of the printing and typesetting industry.</p></div>
  <div class="photo" role="img" aria-label="Tools and cables lying on wiring plans" style="background:linear-gradient(135deg,#e8e6e2,#cfc9c0 50%,#d8a25a)"></div>
</div>
<div class="service" style="left:790px">
  <div class="service-head"><h3 class="heading">Maintenance</h3><p>Lorem Ipsum is the text simply dummy text of the printing and typesetting industry.</p></div>
  <div class="photo" role="img" aria-label="Multimeter testing breakers in a fuse box" style="background:linear-gradient(135deg,#2a2f38,#6b5a3a 50%,#3a6fb0)"></div>
</div>

<section class="gallery">
  <h2 class="heading section-title" style="left:78px;top:56px">Work Gallery</h2>
  <p class="gallery-intro">Offering high value electrical installations, design and maintenance. Focused on custom residential and commercial upgrading.</p>
  <span class="slide-btn" style="left:1032px"><svg width="12" height="16" viewBox="0 0 12 16"><path d="M9 2L3 8l6 6" fill="none" stroke="#fff" stroke-width="2.5"/></svg></span>
  <span class="slide-btn" style="left:1080px"><svg width="12" height="16" viewBox="0 0 12 16"><path d="M3 2l6 6-6 6" fill="none" stroke="#fff" stroke-width="2.5"/></svg></span>
  <div class="photo" role="img" aria-label="Multimeter probes at a breaker panel" style="left:78px;top:187px;width:248px;height:183px;background:linear-gradient(135deg,#d8dadc,#c9a24a 55%,#8c8f94)"></div>
  <div class="photo" role="img" aria-label="Hands fitting a wall socket with a screwdriver" style="left:343px;top:187px;width:248px;height:183px;background:linear-gradient(135deg,#bdbdbd,#e0ddd8 50%,#8a8a8a)"></div>
  <div class="photo" role="img" aria-label="Yellow multimeter testing a distribution board" style="left:607px;top:187px;width:248px;height:183px;background:linear-gradient(135deg,#e9e9e9,#d7b73c 50%,#3f6fa6)"></div>
  <div class="photo" role="img" aria-label="Worker in hard hat inspecting a ceiling installation" style="left:872px;top:187px;width:250px;height:183px;background:linear-gradient(135deg,#dfe5ea,#9fb0bf 50%,#b9c64a)"></div>
</section>

<section class="about" role="img" aria-label="Tangled electrical wiring in dim light">
  <svg style="position:absolute;left:0;top:0" width="1200" height="468" viewBox="0 0 1200 468"><polygon points="1200,0 1200,468 640,468" fill="#5c2a88"/></svg>
  <h2 class="heading section-title" style="left:78px;top:130px">About Us</h2>
  <p>Offering High Value Electrical Installations, Design And Maintenance. Focused On Custom RESIDENTIAL and COMMERCIAL Upgrading. Lighting Design and Application Are Paramount In Our Company's Services.</p>
  <a class="btn" style="left:78px;top:300px;width:166px;height:51px">Learn More</a>
  <div class="photo" role="img" aria-label="Team in yellow hard hats reviewing building plans" style="left:630px;top:62px;width:441px;height:348px;border:3px solid #7a4aa6;background:linear-gradient(135deg,#e6e2da,#e8c53a 45%,#cfc8bc)"></div>
</section>

<section class="contact">
  <h2 class="heading section-title" style="left:0;width:100%;top:56px">Contact Us</h2>
  <p>Lorem Ipsum is simply dummy text of the printing and typesetting industry. Lorem Ipsum has been the industry's standard dummy text ever since the when an unknown printer took a galley.</p>
  <h4>Need An Have Question Please Contact Us !</h4>
  <div class="field focus" style="left:152px;top:234px;width:291px;height:47px">Name *</div>
  <div class="field" style="left:453px;top:234px;width:292px;height:47px">Email *</div>
  <div class="field" style="left:755px;top:234px;width:293px;height:47px">Phone *</div>
  <div class="field" style="left:152px;top:293px;width:896px;height:95px">Message *</div>
  <a class="btn" style="left:152px;top:396px;width:896px;height:51px;font-size:18px">Submit</a>
</section>

<footer class="site-footer">
  <div class="footer-brand"><span class="brand-mark"></span>K7 ELECTRICAL SERVICES</div>
  <span class="social" style="left:511px;background:var(--purple)"></span>
  <span class="social" style="left:573px;background:#666"></span>
  <span class="social" style="left:636px;background:#666"></span>
  <div class="footer-links"><span>Home</span><span>About Us</span><span>Gallery</span><span>Contact</span></div>
  <div class="copyright">©Electrical Services - 2018 All Right Recerved. Privacy Policy &nbsp;|&nbsp; Terms &amp; Conditions</div>
</footer>

</body>
</html>
```